BWP Business Card

A double sided business card based on your "Brindlewood Partners Ltd" Logo. To use the "BWP" logo on 1 side and the full company logo on the reverse.

Detials to be included:

Name: Tomas Wheeler
Postion: Consultant Orthotist & Expert Witness
T: +44 (0) 7700 938271
F: +44 (0) 7654 8820

```html
<!DOCTYPE html>
<html lang="en">
<head>
<meta charset="utf-8">
<title>Brindlewood Partners Ltd – Business Card</title>
<link href="https://fonts.googleapis.com/css2?family=Tinos:wght@400;700&display=swap" rel="stylesheet">
<style>
  :root {
    --navy: #1d3a6b;
    --text-grey: #6f6f6f;
    --text-dark: #333333;
    --rule: #b9b9b9;
    --card: #ffffff;
    --backdrop: #e9e9e9;
  }
  * { box-sizing: border-box; margin: 0; padding: 0; }
  html, body { width: 1200px; height: 720px; overflow: hidden; }
  body {
    background: var(--backdrop);
    font-family: "Tinos", "Times New Roman", serif;
    position: relative;
  }
  .card {
    position: absolute;
    top: 217px;
    width: 500px;
    height: 286px;
    background: var(--card);
    box-shadow: 0 2px 8px rgba(0,0,0,0.12);
    overflow: hidden;
  }
  .card--front { left: 70px; }
  .card--back { left: 630px; display: flex; align-items: center; justify-content: center; }

  .brand { display: flex; align-items: center; gap: 12px; }
  .brand__square { background: var(--navy); flex: none; }
  .brand__name {
    color: var(--navy);
    font-weight: 400;
    line-height: 1.15;
  }

  .card--front .brand { position: absolute; left: 30px; top: 84px; }
  .card--front .brand__square { width: 30px; height: 30px; }
  .card--front .brand__name { font-size: 19px; }

  .card--back .brand { gap: 20px; }
  .card--back .brand__square { width: 56px; height: 56px; }
  .card--back .brand__name { font-size: 34px; }

  .divider {
    position: absolute;
    left: 262px;
    top: 52px;
    width: 1px;
    height: 100px;
    background: var(--rule);
  }

  .contact { position: absolute; left: 282px; top: 50px; }
  .contact__name { color: var(--navy); font-weight: 700; font-size: 16px; margin-bottom: 3px; }
  .contact__role { color: var(--text-grey); font-size: 12.5px; line-height: 1.2; }
  .contact__lines { margin-top: 8px; }
  .contact__line {
    display: flex; align-items: center; gap: 6px;
    color: var(--text-dark); font-size: 12.5px; line-height: 1.55;
  }
  .contact__line svg { width: 11px; height: 11px; fill: var(--text-dark); flex: none; }

  .band { position: absolute; left: 0; top: 0; width: 500px; height: 286px; }
  .address {
    position: absolute; left: 30px; bottom: 30px;
    color: #444; font-size: 11px;
  }
  .email {
    position: absolute; right: 20px; bottom: 31px;
    color: #fff; font-size: 12px;
  }
</style>
</head>
<body>

  <section class="card card--front" aria-label="Business card front">
    <div class="brand">
      <span class="brand__square"></span>
      <div class="brand__name">Brindlewood<br>Partners Ltd</div>
    </div>

    <span class="divider"></span>

    <div class="contact">
      <div class="contact__name">Tomas Wheeler</div>
      <div class="contact__role">Consultant Orthotist</div>
      <div class="contact__role">Expert Witness</div>
      <div class="contact__lines">
        <div class="contact__line">
          <svg viewBox="0 0 24 24" aria-hidden="true"><path d="M6.6 10.8a15.1 15.1 0 0 0 6.6 6.6l2.2-2.2c.3-.3.7-.4 1-.2 1.1.4 2.3.6 3.6.6.6 0 1 .4 1 1V20c0 .6-.4 1-1 1A17 17 0 0 1 3 4c0-.6.4-1 1-1h3.5c.6 0 1 .4 1 1 0 1.3.2 2.5.6 3.6.1.3 0 .7-.2 1z"/></svg>
          +44 (0) 7700 938271
        </div>
        <div class="contact__line">
          <svg viewBox="0 0 24 24" aria-hidden="true"><path d="M7 3h8l2 2v4H7zM4 10h16a2 2 0 0 1 2 2v6h-4v3H6v-3H2v-6a2 2 0 0 1 2-2zm4 6v3h8v-3z"/></svg>
          +44 (0) 7654 8820
        </div>
      </div>
    </div>

    <svg class="band" viewBox="0 0 500 286" aria-hidden="true">
      <path d="M0 262 L285 262 C300 262 302 238 322 238 L500 238 L500 274 L0 274 Z" fill="var(--navy)"/>
    </svg>
    <div class="address">18 Larkfield Road, Kingston, Surrey, KT2 6QR</div>
    <div class="email">tomas@brindlewoodpartners.co.uk</div>
  </section>

  <section class="card card--back" aria-label="Business card back">
    <div class="brand">
      <span class="brand__square"></span>
      <div class="brand__name">Brindlewood<br>Partners Ltd</div>
    </div>
  </section>

</body>
</html>
```